BUSINESS CARD - HALLORAN FIELD SERVICES

I would like to create a business card for my fertilizer spreading business. I would like to incorporate my existing logo and also a description of the services offered. The business card will be given to farmers so must be kept simple but effective. It will also be left in stores so much also be eye catching in order to stand out from other cards.

Target Market(s)

FARMERS

Requirements
Must have
• FRONT OF CARD = EXISTING LOGO + "CUSTOMISED SPREADING" below the logo

REAR Of CARD = SERVICES OFFERED AND CONTACT DETAILS

- Bulk fertilizer including Lime, Gypsum, Manure & Compost
- Granular fertilizer including Single Super, Urea, Gran-am, & Custom Blends
- Modern equipment - Autosteer & Variable Rate Capable
- Friendly & Reliable Service
- Contact Gus: 0417 552 308
Nice to have
• utilize same color scheme as existing logo

```html
<!DOCTYPE html>
<html lang="en">
<head>
<meta charset="utf-8">
<title>Halloran Field Services – Business Card</title>
<link href="https://fonts.googleapis.com/css2?family=Lato:wght@400;700;900&display=swap" rel="stylesheet">
<style>
  :root {
    --backdrop: #3a3c40;
    --card: #ffffff;
    --ink: #555557;
    --ink-soft: #5e5e60;
    --accent: #f0931e;
  }
  * { box-sizing: border-box; margin: 0; padding: 0; }
  html, body {
    width: 1200px;
    height: 900px;
    overflow: hidden;
    background: var(--backdrop);
    font-family: "Lato", sans-serif;
  }
  .sheet {
    width: 1200px;
    height: 900px;
    display: flex;
    flex-direction: column;
    align-items: center;
    justify-content: center;
    gap: 28px;
  }
  .card {
    width: 720px;
    height: 411px;
    background: var(--card);
    border-radius: 18px;
    position: relative;
    box-shadow: 0 10px 30px rgba(0,0,0,0.35);
  }

  /* Front */
  .card--front {
    display: flex;
    flex-direction: column;
    align-items: center;
    justify-content: center;
    gap: 26px;
  }
  .brand {
    display: flex;
    align-items: center;
    gap: 28px;
  }
  .brand-mark {
    width: 150px;
    height: 150px;
    flex: none;
  }
  .brand-name {
    color: var(--ink);
    font-weight: 900;
    font-size: 44px;
    line-height: 1.02;
    letter-spacing: -0.5px;
    text-transform: uppercase;
  }
  .tagline {
    display: flex;
    align-items: center;
    gap: 14px;
    width: 560px;
    color: var(--accent);
    font-weight: 700;
    font-size: 22px;
    letter-spacing: 5px;
    text-transform: uppercase;
    white-space: nowrap;
  }
  .tagline-rule {
    flex: 1;
    height: 3px;
    background: var(--accent);
  }

  /* Back */
  .card--back { padding: 40px 44px; }
  .contact-phone {
    position: absolute;
    top: 38px;
    right: 44px;
    display: flex;
    align-items: center;
    gap: 8px;
    color: var(--ink-soft);
    font-size: 20px;
    letter-spacing: 0.5px;
  }
  .contact-phone svg { width: 20px; height: 20px; }
  .person {
    position: absolute;
    top: 108px;
    left: 44px;
  }
  .person-name {
    color: var(--accent);
    font-weight: 700;
    font-size: 30px;
    line-height: 1;
  }
  .person-role {
    color: var(--ink-soft);
    font-size: 18px;
    margin-top: 4px;
    letter-spacing: 0.3px;
  }
  .services {
    position: absolute;
    left: 150px;
    bottom: 40px;
    list-style: none;
    color: var(--ink-soft);
    font-size: 19px;
    line-height: 1.45;
    letter-spacing: 0.2px;
  }
  .services li { position: relative; padding-left: 22px; }
  .services li.is-bullet::before {
    content: "";
    position: absolute;
    left: 0;
    top: 0.45em;
    width: 13px;
    height: 13px;
    border-radius: 50%;
    background: var(--accent);
  }
</style>
</head>
<body>
  <main class="sheet">
    <section class="card card--front" aria-label="Card front">
      <div class="brand">
        <svg class="brand-mark" viewBox="0 0 150 150" aria-hidden="true">
          <circle cx="75" cy="75" r="70" fill="var(--ink)"/>
        </svg>
        <div class="brand-name">Halloran Field<br>Services</div>
      </div>
      <div class="tagline">
        <span class="tagline-rule"></span>
        <span>Customised Spreading</span>
        <span class="tagline-rule"></span>
      </div>
    </section>

    <section class="card card--back" aria-label="Card back">
      <div class="contact-phone">
        <svg viewBox="0 0 24 24" aria-hidden="true">
          <path fill="var(--accent)" d="M6.6 10.8a15.1 15.1 0 0 0 6.6 6.6l2.2-2.2c.3-.3.7-.4 1-.2 1.1.4 2.3.6 3.6.6.6 0 1 .4 1 1V20c0 .6-.4 1-1 1A17 17 0 0 1 3 4c0-.6.4-1 1-1h3.5c.6 0 1 .4 1 1 0 1.3.2 2.5.6 3.6.1.3 0 .7-.2 1l-2.3 2.2z"/>
        </svg>
        <span>0417 552 308</span>
      </div>

      <div class="person">
        <div class="person-name">Gus</div>
        <div class="person-role">CEO/ General Manager</div>
      </div>

      <ul class="services">
        <li class="is-bullet">Bulk fertilizer including Lime, Gypsum, Manure &amp; Compost.</li>
        <li class="is-bullet">Granular fertilizer including Single Super,</li>
        <li>Urea, Gran-am, &amp; Custom Blends.</li>
        <li class="is-bullet">Modern equipment - Autosteer &amp; Variable Rate Capable.</li>
        <li class="is-bullet">Friendly &amp; Reliable Service.</li>
      </ul>
    </section>
  </main>
</body>
</html>
```